Corporate Trainning business needs PPT template for sales, reports and projects

Create a power point template with own design and rich in distinctness of our brand, logo and industry (corporate training). Enough slides templates to use for sales, reports and projects development: flowcharts, roadmaps, bullets, service categories, description box, title & subtitle slides, bar & pie charts, calendars, gantt, some basic shapes and icons (training, education, elearning, etc related).
Enclose: color palette, set of logo for different uses and ppt presentation with some ideas and slide templates. The ppt hope could help, but I trust in your experience and creativity.

Target Market(s)

Company training

Industry/Entity Type

Training - Education

Font styles to use
Sans Serif

Requirements
Nice to have
• Relative to training icons

```html
<!DOCTYPE html>
<html lang="en">
<head>
<meta charset="utf-8">
<title>Summitra – Presentation Template</title>
<link href="https://fonts.googleapis.com/css2?family=Roboto:wght@400;500;700;900&display=swap" rel="stylesheet">
<style>
  :root {
    --navy: #10223f;
    --yellow: #e3b71c;
    --canvas: #dcdee1;
    --white: #ffffff;
    --ink: #1d1d1f;
    --grey-text: #4a4a4a;
    --cell-grey: #c9cacc;
  }
  * { box-sizing: border-box; margin: 0; padding: 0; }
  html, body { width: 1200px; height: 4231px; overflow: hidden; }
  body { background: var(--canvas); font-family: "Roboto", Arial, sans-serif; color: var(--ink); position: relative; }
  .slide { position: absolute; left: 36px; width: 1130px; height: 635px; overflow: hidden; background: var(--white); box-shadow: 0 2px 6px rgba(0,0,0,.18); }
  .abs { position: absolute; }
  .photo { position: absolute; }

  /* Slide 1 – cover */
  .cover { top: 54px; }
  .cover .photo { inset: 0; background: linear-gradient(135deg, #2a2c30 0%, #3a3630 45%, #22252a 100%); }
  .brand-lockup { position: absolute; left: 342px; top: 249px; width: 480px; height: 135px; }
  .brand-mark { position: absolute; left: 0; top: 12px; width: 104px; height: 104px; border-radius: 50%; background: var(--yellow); }
  .brand-name { position: absolute; left: 128px; top: 0; font-size: 84px; font-weight: 500; color: var(--white); line-height: 1; letter-spacing: 1px; }
  .cover-subtitle { position: absolute; left: 0; top: 400px; width: 100%; text-align: center; font-size: 18px; font-weight: 400; letter-spacing: 3px; color: var(--white); }

  /* Slide 2 – solutions */
  .solutions { top: 749px; }
  .solutions svg.bg { position: absolute; inset: 0; }
  .card { position: absolute; width: 195px; background: var(--white); text-align: center; padding: 14px 12px 0; box-shadow: 0 1px 4px rgba(0,0,0,.12); }
  .card svg { width: 42px; height: 42px; stroke: var(--navy); fill: none; stroke-width: 1.8; stroke-linecap: round; stroke-linejoin: round; }
  .card h3 { font-size: 16px; font-weight: 700; color: var(--ink); margin: 8px 0 7px; }
  .card p { font-size: 10.5px; line-height: 17px; color: var(--grey-text); }
  .solutions-title { position: absolute; left: 32px; top: 575px; color: var(--white); font-size: 31px; font-weight: 700; letter-spacing: .5px; }

  /* Slide 3 – calendar */
  .calendar-slide { top: 1445px; }
  .slide-heading { position: absolute; left: 0; width: 100%; text-align: center; font-size: 38px; font-weight: 900; color: var(--ink); }
  .calendar-slide .slide-heading { top: 50px; z-index: 2; }
  .feature { position: absolute; left: 30px; width: 400px; }
  .feature h3 { font-size: 21px; font-weight: 700; color: var(--navy); margin-bottom: 12px; }
  .feature h3 span { color: var(--yellow); }
  .feature p { font-size: 12.5px; line-height: 24px; color: var(--grey-text); }
  .ring { position: absolute; border-radius: 50%; border-style: solid; border-color: var(--yellow); }
  .laptop-screen { position: absolute; left: 566px; top: 175px; width: 462px; height: 302px; background: #1b1c1f; border-radius: 12px 12px 0 0; }
  .laptop-display { position: absolute; left: 574px; top: 185px; width: 446px; height: 287px; background: var(--white); }
  .laptop-base { position: absolute; left: 499px; top: 477px; width: 608px; height: 48px; }
  .cal-month { position: absolute; left: 586px; top: 196px; font-size: 13px; font-weight: 700; }
  .cal-rule { position: absolute; left: 848px; top: 205px; width: 150px; height: 1px; background: #888; }
  .cal-days, .cal-grid { position: absolute; left: 585px; width: 413px; display: grid; grid-template-columns: repeat(7, 1fr); }
  .cal-days { top: 233px; font-size: 10px; text-align: right; }
  .cal-days span { padding-right: 6px; }
  .cal-grid { top: 249px; grid-template-rows: repeat(5, 41.4px); border-left: 1px solid #333; border-top: 1px solid #333; }
  .cal-grid span { border-right: 1px solid #333; border-bottom: 1px solid #333; font-size: 11px; text-align: right; padding: 1px 4px 0 0; }
  .cal-grid .off { background: var(--cell-grey); }

  /* Slide 4 – steps */
  .steps-slide { top: 2136px; }
  .step { position: absolute; top: 62px; width: 200px; text-align: center; }
  .step svg { width: 50px; height: 50px; stroke: var(--navy); fill: none; stroke-width: 1.8; stroke-linecap: round; stroke-linejoin: round; }
  .step svg .accent { stroke: var(--yellow); }
  .step h3 { font-size: 16px; font-weight: 500; margin: 8px 0 10px; }
  .step p { font-size: 11.5px; line-height: 21px; color: var(--grey-text); }
  .timeline { position: absolute; left: 123px; top: 264px; width: 883px; height: 7px; border-radius: 4px; background: var(--yellow); }
  .dot { position: absolute; top: 259px; width: 17px; height: 17px; border-radius: 50%; background: var(--navy); }
  .date { position: absolute; top: 293px; width: 100px; text-align: center; font-size: 16px; font-weight: 700; }
  .steps-band { left: 0; top: 358px; width: 1130px; height: 277px; background: linear-gradient(120deg, #2c2e31, #3b3a37 50%, #262829); }
  .band-title { position: absolute; left: 0; top: 473px; width: 100%; text-align: center; color: var(--white); font-size: 40px; font-weight: 700; }

  /* Slide 5 – services */
  .services { top: 2835px; }
  .block-yellow { left: 868px; top: 0; width: 262px; height: 202px; background: var(--yellow); }
  .block-navy { left: 0; top: 435px; width: 261px; height: 200px; background: var(--navy); }
  .services .photo { left: 89px; top: 46px; width: 952px; height: 545px; background: linear-gradient(135deg, #6f7378 0%, #8a8578 40%, #5a5f66 100%); }
  .services-title { position: absolute; left: 89px; top: 295px; width: 952px; text-align: center; color: var(--white); font-size: 40px; font-weight: 700; }

  /* Slide 6 – closing */
  .closing { top: 3549px; }
  .closing .photo-scene { inset: 0; background: linear-gradient(120deg, #4b5a6a 0%, #7a6a5c 55%, #5c4a40 100%); }
  .closing .photo-person { left: 480px; top: 60px; width: 380px; height: 575px; border-radius: 190px 190px 0 0; background: linear-gradient(180deg, #8a6a55 0%, #3f4a5c 40%, #2e3646 100%); }
  .thank-you { position: absolute; left: 38px; top: 136px; writing-mode: vertical-rl; color: var(--white); font-size: 60px; font-weight: 900; letter-spacing: 1px; line-height: 1; }
</style>
</head>
<body>

<!-- Cover -->
<section class="slide cover">
  <div class="photo" role="img" aria-label="Photo of a trainer presenting charts to a seated team in a brick-walled office, darkened"></div>
  <div class="brand-lockup">
    <div class="brand-mark"></div>
    <div class="brand-name">Summitra</div>
  </div>
  <p class="cover-subtitle">LEARN AND LEAD</p>
</section>

<!-- Solutions -->
<section class="slide solutions">
  <svg class="bg" width="1130" height="635" viewBox="0 0 1130 635">
    <rect width="1130" height="635" fill="#8b8276" role="img" aria-label="Photo of colleagues smiling in a meeting in a bright office"/>
    <polygon points="0,327 651,327 802,574 1130,574 1130,635 0,635" fill="#10223f"/>
    <polyline points="0,327 651,327 802,574 1130,574" fill="none" stroke="#e3b71c" stroke-width="7"/>
  </svg>

  <div class="card" style="left:31px;top:163px;height:164px;">
    <svg viewBox="0 0 40 40"><rect x="8" y="6" width="20" height="26" rx="2"/><path d="M14 4h16l4 4v24"/><path d="M18 13l2 4 4 .5-3 3 .8 4-3.8-2-3.8 2 .8-4-3-3 4-.5z"/></svg>
    <h3>Brand ID</h3>
    <p>Lorem ipsum dolor sit amet, consectetur adipiscing elit, sed do eiusmod tempor incididunt</p>
  </div>
  <div class="card" style="left:240px;top:192px;height:172px;">
    <svg viewBox="0 0 40 40"><path d="M24 6c6-2 10-2 10-2s0 4-2 10L20 26l-6-6z"/><circle cx="26" cy="14" r="3"/><path d="M14 20l-6 1 4-6h6M20 26l-1 6 6-4v-6M10 30l-4 4M14 32l-2 2M8 26l-2 2"/></svg>
    <h3>Startup Support</h3>
    <p>Lorem ipsum dolor sit amet, consectetur adipiscing elit, sed do eiusmod tempor incididunt</p>
  </div>
  <div class="card" style="left:452px;top:163px;height:164px;">
    <svg viewBox="0 0 40 40"><path d="M10 6l5 0 3 7-4 3c2 4 5 7 9 9l3-4 7 3v5c0 2-2 3-4 3C17 31 9 23 7 9c0-2 1-3 3-3z"/><path d="M24 6a10 10 0 0 1 10 10M24 11a5 5 0 0 1 5 5"/></svg>
    <h3>Call Center</h3>
    <p>Lorem ipsum dolor sit amet, consectetur adipiscing elit, sed do eiusmod tempor incididunt</p>
  </div>
  <div class="card" style="left:31px;top:348px;height:173px;">
    <svg viewBox="0 0 40 40"><rect x="4" y="6" width="24" height="20" rx="1"/><circle cx="12" cy="14" r="4"/><path d="M19 12h5M19 16h5M8 22h12"/><circle cx="28" cy="26" r="6"/><path d="M32 30l5 5"/></svg>
    <h3>Market Research</h3>
    <p>Lorem ipsum dolor sit amet, consectetur adipiscing elit, sed do eiusmod tempor incididunt</p>
  </div>
  <div class="card" style="left:240px;top:378px;height:172px;">
    <svg viewBox="0 0 40 40"><path d="M20 3l13 5v10c0 9-6 15-13 19C13 33 7 27 7 18V8z"/><rect x="14" y="18" width="12" height="9" rx="1"/><path d="M16 18v-3a4 4 0 0 1 8 0v3"/></svg>
    <h3>Security Control</h3>
    <p>Lorem ipsum dolor sit amet, consectetur adipiscing elit, sed do eiusmod tempor incididunt</p>
  </div>
  <div class="card" style="left:452px;top:348px;height:173px;">
    <svg viewBox="0 0 40 40"><rect x="13" y="13" width="14" height="14" rx="2"/><circle cx="7" cy="7" r="4"/><circle cx="33" cy="7" r="4"/><circle cx="7" cy="33" r="4"/><circle cx="33" cy="33" r="4"/><path d="M10 10l3 3M30 10l-3 3M10 30l3-3M30 30l-3-3"/></svg>
    <h3>Social Media</h3>
    <p>Lorem ipsum dolor sit amet, consectetur adipiscing elit, sed do eiusmod tempor incididunt</p>
  </div>

  <h2 class="solutions-title">SUMMITRA SOLUTIONS</h2>
</section>

<!-- Calendar -->
<section class="slide calendar-slide">
  <div class="ring" style="left:552px;top:66px;width:492px;height:492px;border-width:41px;"></div>
  <h2 class="slide-heading">CALENDAR OPTION</h2>

  <div class="feature" style="top:177px;">
    <h3>Be A Part Of The <span>Revolution</span></h3>
    <p>Lorem ipsum dolor sit amet, consectetur adipiscing elit, sed do eiusmod tempor incididunt ut labore et dolore magna aliqua. Ut enim ad minim veniam, quis nostrud</p>
  </div>
  <div class="feature" style="top:306px;">
    <h3>Unique Opportunity To <span>Grow</span></h3>
    <p>Lorem ipsum dolor sit amet, consectetur adipiscing elit, sed do eiusmod tempor incididunt ut labore et dolore magna aliqua. Ut enim ad minim veniam, quis nostrud</p>
  </div>
  <div class="feature" style="top:435px;">
    <h3>Find Your Own <span>Future</span></h3>
    <p>Lorem ipsum dolor sit amet, consectetur adipiscing elit, sed do eiusmod tempor incididunt ut labore et dolore magna aliqua. Ut enim ad minim veniam, quis nostrud</p>
  </div>

  <div class="laptop-screen"></div>
  <div class="laptop-display"></div>
  <svg class="laptop-base" viewBox="0 0 608 48">
    <path d="M0 4h608v10c0 6-20 14-40 14H40C20 28 0 20 0 14z" fill="#2e2f33"/>
    <rect x="210" y="4" width="188" height="6" rx="3" fill="#55565b"/>
    <rect x="250" y="20" width="108" height="3" rx="1.5" fill="#d9d9d9"/>
  </svg>
  <div class="cal-month">JUNE 2022</div>
  <div class="cal-rule"></div>
  <div class="cal-days"><span>S</span><span>M</span><span>T</span><span>W</span><span>T</span><span>F</span><span>S</span></div>
  <div class="cal-grid">
    <span class="off"></span><span class="off"></span><span class="off"></span><span>1</span><span>2</span><span>3</span><span>4</span>
    <span>5</span><span>6</span><span>7</span><span>8</span><span>9</span><span>10</span><span>11</span>
    <span>12</span><span>13</span><span>14</span><span>15</span><span>16</span><span>17</span><span>18</span>
    <span>19</span><span>20</span><span>21</span><span>22</span><span>23</span><span>24</span><span>25</span>
    <span>26</span><span>27</span><span>28</span><span>29</span><span>30</span><span class="off"></span><span class="off"></span>
  </div>
</section>

<!-- Four steps -->
<section class="slide steps-slide">
  <div class="step" style="left:118px;">
    <svg viewBox="0 0 50 50"><circle class="accent" cx="17" cy="14" r="6"/><circle class="accent" cx="17" cy="14" r="2"/><path d="M6 36l8-4h10c2 0 2 3 0 3h-8M24 35l10-6c2-1 3 1 2 2l-12 9H6"/><circle cx="38" cy="8" r="2.5"/><circle cx="38" cy="18" r="2.5"/><path d="M38 10.5v5"/></svg>
    <h3>Step 1</h3>
    <p>Lorem ipsum dolor sit amet, consectetur adipiscing elit, sed do eiusmod tempor incididunt ut labore et dolore magna aliqua.</p>
  </div>
  <div class="step" style="left:350px;">
    <svg viewBox="0 0 50 50"><rect x="8" y="10" width="34" height="24" rx="1"/><path d="M14 28l7-7 5 4 9-9M31 16h4v4"/><circle class="accent" cx="14" cy="7" r="4"/><path d="M14 40v-6M36 40v-6M10 44h8"/></svg>
    <h3>Step 2</h3>
    <p>Lorem ipsum dolor sit amet, consectetur adipiscing elit, sed do eiusmod tempor incididunt ut labore et dolore magna aliqua.</p>
  </div>
  <div class="step" style="left:581px;">
    <svg viewBox="0 0 50 50"><path d="M10 40V6h20l6 6v8"/><path d="M15 13h10M15 18h14M15 23h8"/><rect x="20" y="28" width="24" height="16" rx="2"/><path d="M28 28v-3h8v3M20 35h24"/><circle class="accent" cx="40" cy="8" r="4"/></svg>
    <h3>Step 3</h3>
    <p>Lorem ipsum dolor sit amet, consectetur adipiscing elit, sed do eiusmod tempor incididunt ut labore et dolore magna aliqua.</p>
  </div>
  <div class="step" style="left:813px;">
    <svg viewBox="0 0 50 50"><circle class="accent" cx="25" cy="9" r="5"/><circle cx="14" cy="20" r="4"/><circle cx="36" cy="20" r="4"/><path d="M6 34c0-6 4-9 8-9s6 2 7 4M44 34c0-6-4-9-8-9s-6 2-7 4"/><path d="M14 36l6-5 5 3 5-3 6 5-8 6-3-2-3 2z"/></svg>
    <h3>Step 4</h3>
    <p>Lorem ipsum dolor sit amet, consectetur adipiscing elit, sed do eiusmod tempor incididunt ut labore et dolore magna aliqua.</p>
  </div>

  <div class="timeline"></div>
  <div class="dot" style="left:209px;"></div>
  <div class="dot" style="left:441px;"></div>
  <div class="dot" style="left:673px;"></div>
  <div class="dot" style="left:905px;"></div>
  <div class="date" style="left:168px;">01 Jun</div>
  <div class="date" style="left:400px;">15 Jul</div>
  <div class="date" style="left:631px;">01 Aug</div>
  <div class="date" style="left:863px;">15 Sep</div>

  <div class="photo steps-band" role="img" aria-label="Photo of a team discussing around a meeting table, darkened"></div>
  <h2 class="band-title">FOUR STEPS PROCESS</h2>
</section>

<!-- Services -->
<section class="slide services">
  <div class="abs block-yellow"></div>
  <div class="abs block-navy"></div>
  <div class="photo" role="img" aria-label="Photo of colleagues working together at a conference table with papers and laptops"></div>
  <h2 class="services-title">OUR SERVICES</h2>
</section>

<!-- Closing -->
<section class="slide closing">
  <div class="photo photo-scene" role="img" aria-label="Blurred photo of an office with people working at desks"></div>
  <div class="ring" style="left:423px;top:46px;width:476px;height:476px;border-width:40px;"></div>
  <div class="photo photo-person" role="img" aria-label="Photo of a smiling businessman in a grey blazer, standing with hands in pockets"></div>
  <h2 class="thank-you">THANK YOU</h2>
</section>

</body>
</html>
```